Vantro cards

I am in the auto motive, transportation business I would like a business card that is Something cool, modern edgy, having to do with car culture. I offer towing service for high and exotic cars. I also provide towing for collisions and car accidents. I offer open and enclosed transport nationwide.

Target Market(s)

Car culture people high end auto collectors

Industry/Entity Type

Towing car carrier

Contact Information for Business Card

My company colors black yellow and silver

Font styles to use
Serif

```html
<!DOCTYPE html>
<html lang="en">
<head>
<meta charset="utf-8">
<title>Vantro cards</title>
<link rel="stylesheet" href="https://fonts.googleapis.com/css2?family=Montserrat:wght@700;800&family=Arimo:wght@400&display=swap">
<style>
  :root {
    --stage: #2a2a2a;
    --card-dark: #1a1a1a;
    --card-light: #ffffff;
    --ink: #111111;
    --brand-yellow: #f7df5c;
    --silver: #d9d9d9;
    --rule: #bdbdbd;
  }
  html, body {
    margin: 0;
    padding: 0;
    width: 1200px;
    height: 1040px;
    overflow: hidden;
    background: var(--stage);
  }
  .canvas {
    position: relative;
    width: 1200px;
    height: 1040px;
  }
  .card {
    position: absolute;
    left: 290px;
    width: 620px;
    height: 354px;
    border-radius: 0 64px 0 64px;
    box-sizing: border-box;
    box-shadow: 0 8px 24px rgba(0,0,0,.45);
  }
  .card--back {
    top: 110px;
    background: var(--card-dark);
    display: flex;
    align-items: center;
    justify-content: center;
  }
  .card--front {
    top: 556px;
    background: var(--card-light);
    display: flex;
    align-items: center;
  }
  .brand {
    display: flex;
    align-items: center;
    gap: 14px;
    font-family: "Montserrat", sans-serif;
    font-weight: 800;
    font-size: 58px;
    letter-spacing: 2px;
    text-transform: uppercase;
  }
  .brand__mark {
    width: 26px;
    height: 26px;
    background: var(--brand-yellow);
  }
  .card--back .brand { color: var(--silver); }
  .card--front .brand {
    color: var(--ink);
    font-size: 46px;
  }
  .front__logo {
    width: 320px;
    display: flex;
    justify-content: center;
  }
  .front__divider {
    width: 1px;
    height: 180px;
    background: var(--rule);
  }
  .contact {
    padding-left: 28px;
    font-family: "Arimo", sans-serif;
    color: var(--ink);
  }
  .contact__name {
    margin: 0;
    font-family: "Montserrat", sans-serif;
    font-weight: 700;
    font-size: 20px;
    letter-spacing: 1px;
    text-transform: uppercase;
  }
  .contact__role {
    margin: 2px 0 16px;
    font-size: 16px;
  }
  .contact__list {
    list-style: none;
    margin: 0 0 14px;
    padding: 0;
    font-size: 16px;
    line-height: 1.45;
  }
  .contact__list li {
    display: flex;
    align-items: center;
    gap: 8px;
  }
  .contact__list svg {
    width: 15px;
    height: 15px;
    flex: none;
  }
  .contact__address {
    margin: 0;
    font-style: normal;
    font-size: 16px;
    line-height: 1.35;
  }
</style>
</head>
<body>
<main class="canvas">
  <section class="card card--back" aria-label="Card back">
    <div class="brand"><span class="brand__mark"></span>Vantro</div>
  </section>

  <section class="card card--front" aria-label="Card front">
    <div class="front__logo">
      <div class="brand"><span class="brand__mark"></span>Vantro</div>
    </div>
    <div class="front__divider"></div>
    <div class="contact">
      <h1 class="contact__name">Marcus Hale</h1>
      <p class="contact__role">Managing Director</p>
      <ul class="contact__list">
        <li>
          <svg viewBox="0 0 24 24" aria-hidden="true"><path d="M6.6 10.8a15.1 15.1 0 0 0 6.6 6.6l2.2-2.2a1 1 0 0 1 1-.25 11.4 11.4 0 0 0 3.6.57 1 1 0 0 1 1 1V20a1 1 0 0 1-1 1A17 17 0 0 1 3 4a1 1 0 0 1 1-1h3.5a1 1 0 0 1 1 1c0 1.25.2 2.45.57 3.57a1 1 0 0 1-.25 1z" fill="none" stroke="#111" stroke-width="2"/></svg>
          044-987 654 321
        </li>
        <li>
          <svg viewBox="0 0 24 24" aria-hidden="true"><rect x="2" y="5" width="20" height="14" fill="#111"/><path d="M2 5l10 8 10-8" fill="none" stroke="#fff" stroke-width="1.5"/></svg>
          info@vantrotow.com
        </li>
        <li>
          <svg viewBox="0 0 24 24" aria-hidden="true"><g fill="none" stroke="#111" stroke-width="1.8"><circle cx="12" cy="12" r="10"/><ellipse cx="12" cy="12" rx="4.5" ry="10"/><path d="M2 12h20M4 7h16M4 17h16"/></g></svg>
          www.vantrotow.com
        </li>
      </ul>
      <address class="contact__address">88, Carrier Road<br>60318, Northland</address>
    </div>
  </section>
</main>
</body>
</html>
```